Veltrano.co - Polar Expeditions Specialists

We need a modern, visually striking business card for Veltrano.co, a company specialized in selling expedition cruises to the most remote regions on Earth, with a focus on the Arctic and Antarctica. The design should instantly communicate that the cardholder is an expert in polar travel. Use clean, premium aesthetics with cool tones like icy blue and white, possibly incorporating polar imagery (ice, glaciers, penguins, etc.)

Attached the logo

Contact Information for Business Card

Feels high-end and trustworthy.. Visually memorable — encourages people to keep it

Colors
0054AA
0677BA
7BADD7
CADEEF
E8F1F8

Requirements
Must have
• ice, glaciers, penguins, montains
Nice to have
• modern, transparente,

```html
<!DOCTYPE html>
<html lang="en">
<head>
<meta charset="utf-8">
<title>Veltrano.co — Business Card</title>
<link href="https://fonts.googleapis.com/css2?family=Poppins:wght@400;500;600;700&display=swap" rel="stylesheet">
<style>
  :root {
    --backdrop: #1d1d21;
    --navy: #11122b;
    --navy-soft: #1b1f42;
    --polar-blue: #3373b5;
    --ice-blue: #7badd7;
    --ice-pale: #cadeef;
    --white: #ffffff;
  }
  * { margin: 0; padding: 0; box-sizing: border-box; }
  html, body {
    width: 1200px; height: 900px; overflow: hidden;
    background: var(--backdrop);
    font-family: "Poppins", sans-serif;
  }
  .sheet {
    width: 1200px; height: 900px;
    display: flex; flex-direction: column;
    align-items: center; justify-content: center; gap: 56px;
  }
  .card {
    position: relative;
    width: 620px; height: 354px;
    border-radius: 26px;
    background: var(--navy);
    overflow: hidden;
    box-shadow: 0 18px 40px rgba(0,0,0,.45);
  }

  /* Front */
  .card-front {
    display: flex; flex-direction: column;
    align-items: center; justify-content: center;
  }
  .brand-backdrop {
    position: absolute;
    right: -40px; top: 40px;
    width: 300px; height: 340px;
    border-radius: 140px 140px 0 0;
    background: linear-gradient(180deg, var(--navy-soft) 0%, rgba(27,31,66,.4) 100%);
  }
  .brand-mark {
    position: relative;
    width: 70px; height: 70px;
    border-radius: 50%;
    background: var(--white);
    margin-bottom: 18px;
  }
  .brand-name {
    position: relative;
    color: var(--white);
    font-weight: 700;
    font-size: 64px;
    line-height: 1;
    letter-spacing: 1px;
  }
  .brand-tagline {
    position: relative;
    margin-top: 10px;
    color: var(--white);
    font-weight: 500;
    font-size: 19px;
    letter-spacing: .4px;
  }

  /* Back */
  .accent-bar {
    position: absolute; left: 0; top: 70px;
    width: 10px; height: 44px;
    background: var(--polar-blue);
  }
  .contact-block {
    position: absolute; left: 0; top: 64px;
    padding-left: 44px;
    color: var(--white);
    z-index: 1;
  }
  .person-name {
    color: var(--polar-blue);
    font-weight: 600;
    font-size: 30px;
    line-height: 1.1;
  }
  .person-role { font-size: 17px; margin-top: 2px; }
  .address { font-size: 16px; line-height: 1.45; margin-top: 20px; }
  .contact-list { list-style: none; margin-top: 14px; font-size: 16px; line-height: 1.5; }
  .contact-list li { display: flex; align-items: center; gap: 10px; margin-left: -24px; }
  .contact-list svg { width: 14px; height: 14px; flex: none; }

  .polar-artwork {
    position: absolute;
    left: 330px; top: 96px;
    width: 320px; height: 290px;
    border-radius: 170px 90px 0 0;
    background: linear-gradient(120deg, var(--polar-blue) 0%, var(--polar-blue) 55%, var(--ice-blue) 68%, var(--ice-pale) 78%, var(--white) 100%);
  }
</style>
</head>
<body>
<main class="sheet">

  <section class="card card-front">
    <div class="brand-backdrop" role="img" aria-label="Faint large brand symbol in the background"></div>
    <span class="brand-mark"></span>
    <h1 class="brand-name">Veltrano.co</h1>
    <p class="brand-tagline">Polar Expeditions Specialists</p>
  </section>

  <section class="card card-back">
    <span class="accent-bar"></span>
    <div class="contact-block">
      <h2 class="person-name">Marlow Keane</h2>
      <p class="person-role">CEO &amp; Founder</p>
      <p class="address">48 Harbor Point Drive,<br>Halden, ME 04123 USA</p>
      <ul class="contact-list">
        <li>
          <svg viewBox="0 0 16 16" aria-hidden="true"><path fill="#3373b5" d="M3 1.5l3 .5 1 3-1.6 1.2a8 8 0 0 0 4.4 4.4L11 9l3 1 .5 3-2 1.5C6.5 14 2 9.5 1.5 3.5z"/></svg>
          +1.555.204.318
        </li>
        <li>
          <svg viewBox="0 0 16 16" aria-hidden="true"><rect x="1" y="3" width="14" height="10" rx="1.5" fill="#3373b5"/><path d="M1.5 4l6.5 5 6.5-5" fill="none" stroke="#11122b" stroke-width="1.3"/></svg>
          info@veltranomail.com
        </li>
        <li>
          <svg viewBox="0 0 16 16" aria-hidden="true"><circle cx="8" cy="8" r="6.5" fill="#3373b5"/><path d="M1.5 8h13M8 1.5c-3 3.5-3 9.5 0 13M8 1.5c3 3.5 3 9.5 0 13" fill="none" stroke="#11122b" stroke-width="1.1"/></svg>
          www.veltrano-travel.com
        </li>
      </ul>
    </div>
    <div class="polar-artwork" role="img" aria-label="Polar illustration: a blue polar bear silhouette over icy white glacier light, with two white penguins in front and small stars in the night sky"></div>
  </section>

</main>
</body>
</html>
```